Awesome Digital Ad Design – Vexora Adloop

I am going to be setting up a Vexora Adloop ad campaign I need creatives for.

Several sizes are needed in the end, however, please submit your design concept in the following 2 sizes to start:
Medium rectangle: 300X250
Leaderboard: 728X90

Original artwork/design files and images used expected upon payment and as part of the final delivery.

Ads should match our company brand and the information on this webpage: http://www.harbelstandwork.com/real-estate-marketing/
SEE MORE INSTRUCTIONS IN ATTACHED WORD DOC

Target Market(s)

Business-To-Business Audience –Real Estate Company Executives (Presidents/VPs/Owners/CEOs/Sales Managers).

Industry/Entity Type

Real Estate

Font styles to use
Sans Serif

Requirements
Must have
• Copy should be minimal words, billboard like. Please use real photos/images that would appeal to real estate high-level decision-maker executives.
Should not have
• No cartoons or graphics

```html
<!DOCTYPE html>
<html lang="en">
<head>
<meta charset="utf-8">
<title>Harbel Standwork – Display Ad Concepts</title>
<link rel="stylesheet" href="https://fonts.googleapis.com/css2?family=Roboto+Condensed:wght@400;700&display=swap">
<style>
  :root {
    --board: #2d2d2d;
    --maroon: #722c3c;
    --gold: #c9b37a;
    --white: #ffffff;
    --steel: #4e7a90;
    --orange: #ee6a2b;
    --orange-dark: #d9531a;
    --photo-light: #e9e6e6;
    --photo-mid: #a9adb8;
    --photo-dark: #5d6372;
  }
  * { margin: 0; padding: 0; box-sizing: border-box; }
  html, body { width: 1200px; height: 1200px; overflow: hidden; background: var(--board); }
  body { position: relative; font-family: "Roboto Condensed", "Arial Narrow", sans-serif; }

  .photo {
    position: absolute;
    background:
      radial-gradient(circle at 70% 72%, rgba(255,190,120,.55) 0, rgba(255,190,120,0) 9%),
      linear-gradient(180deg, var(--photo-light) 0%, #d4d4da 38%, var(--photo-mid) 68%, var(--photo-dark) 100%);
  }

  .brand-name {
    color: var(--maroon);
    font-weight: 700;
    text-align: center;
    line-height: 1.05;
    display: flex; flex-direction: column; align-items: center; justify-content: center; gap: 6px;
  }
  .brand-dot { width: 14px; height: 14px; border-radius: 50%; background: var(--steel); }

  .cta {
    position: absolute;
    display: flex; align-items: center; gap: 8px;
    background: linear-gradient(180deg, #f27a3c 0%, var(--orange) 55%, var(--orange-dark) 100%);
    border: 2px solid #f7a070;
    border-radius: 5px;
    color: var(--white);
    font-weight: 700;
    letter-spacing: -0.5px;
    text-transform: uppercase;
    white-space: nowrap;
    line-height: 1;
  }
  .cta svg { flex: none; }
  .cta .cta-label { flex: 1; text-align: center; }

  .accent { color: var(--gold); }

  /* Medium rectangle */
  .ad-rect { position: absolute; left: 208px; top: 98px; width: 784px; height: 654px; background: var(--white); overflow: hidden; }
  .ad-rect .photo { left: 0; top: 0; width: 784px; height: 361px; }
  .ad-rect .shapes { position: absolute; left: 0; top: 0; }
  .ad-rect .logo-box { position: absolute; left: 337px; top: 0; width: 111px; height: 113px; background: var(--white); }
  .ad-rect .brand-name { width: 100%; height: 100%; font-size: 20px; }
  .ad-rect .headline { position: absolute; left: 0; top: 386px; width: 784px; text-align: center; color: var(--white); font-weight: 700; text-transform: uppercase; line-height: 1; white-space: nowrap; }
  .ad-rect .headline .line-1 { font-size: 54px; letter-spacing: -0.5px; }
  .ad-rect .headline .line-2 { font-size: 40px; margin-top: 17px; letter-spacing: -0.4px; }
  .ad-rect .cta { left: 338px; top: 560px; width: 365px; height: 68px; padding: 0 14px 0 16px; font-size: 36px; }

  /* Leaderboard */
  .ad-leader { position: absolute; left: 56px; top: 915px; width: 1088px; height: 134px; background: var(--white); overflow: hidden; }
  .ad-leader .photo { left: 430px; top: 0; width: 658px; height: 134px;
    background:
      radial-gradient(circle at 78% 45%, rgba(255,190,120,.5) 0, rgba(255,190,120,0) 10%),
      linear-gradient(180deg, var(--photo-light) 0%, #d4d4da 38%, var(--photo-mid) 68%, var(--photo-dark) 100%); }
  .ad-leader .shapes { position: absolute; left: 0; top: 0; }
  .ad-leader .logo-area { position: absolute; left: 0; top: 0; width: 180px; height: 134px; }
  .ad-leader .brand-name { width: 100%; height: 100%; font-size: 19px; }
  .ad-leader .copy { position: absolute; left: 170px; top: 0; width: 284px; height: 134px; text-align: center; color: var(--white); font-weight: 700; text-transform: uppercase; font-size: 24px; line-height: 23px; white-space: nowrap; }
  .ad-leader .copy .block { padding-top: 10px; }
  .ad-leader .copy .divider { position: absolute; left: 18px; right: 0; top: 66px; border-top: 1px dotted rgba(255,255,255,.55); }
  .ad-leader .copy .block-2 { position: absolute; left: 0; right: 0; top: 75px; }
  .ad-leader .cta { left: 862px; top: 75px; width: 208px; height: 39px; padding: 0 6px 0 8px; gap: 4px; font-size: 21px; }
</style>
</head>
<body>

  <section class="ad-rect" aria-label="Medium rectangle ad">
    <div class="photo" role="img" aria-label="Business handshake double-exposed with a city skyline and office professionals"></div>
    <svg class="shapes" width="784" height="654" viewBox="0 0 784 654">
      <rect x="0" y="361" width="784" height="14" fill="var(--steel)"/>
      <path d="M0 375 H784 V528 Q300 520 0 654 Z" fill="var(--maroon)"/>
    </svg>
    <div class="logo-box">
      <div class="brand-name"><span class="brand-dot"></span>Harbel<br>Standwork</div>
    </div>
    <h1 class="headline">
      <div class="line-1">Client Follow-Up <span class="accent">Made Simple</span></div>
      <div class="line-2">Virtually No Cost To <span class="accent">Your Company!</span></div>
    </h1>
    <a class="cta">
      <svg width="42" height="42" viewBox="0 0 24 24" aria-hidden="true"><path fill="#fff" d="M6.6 10.8a15 15 0 0 0 6.6 6.6l2.2-2.2c.3-.3.7-.4 1-.2 1.1.4 2.3.6 3.6.6.6 0 1 .4 1 1V20c0 .6-.4 1-1 1A17 17 0 0 1 3 4c0-.6.4-1 1-1h3.5c.6 0 1 .4 1 1 0 1.3.2 2.5.6 3.6.1.3 0 .7-.2 1z"/><path d="M14 3a7 7 0 0 1 7 7M14 6.5a3.5 3.5 0 0 1 3.5 3.5" stroke="#fff" stroke-width="1.6" fill="none"/></svg>
      <span class="cta-label">Call To Action</span>
      <svg width="52" height="52" viewBox="0 0 24 24" aria-hidden="true"><circle cx="12" cy="12" r="10.5" fill="#fff"/><path d="M7 10h5V6.5L17.5 12 12 17.5V14H7z" fill="var(--orange)"/></svg>
    </a>
  </section>

  <section class="ad-leader" aria-label="Leaderboard ad">
    <div class="photo" role="img" aria-label="Business handshake double-exposed with a city skyline and office professionals"></div>
    <svg class="shapes" width="1088" height="134" viewBox="0 0 1088 134">
      <polygon points="176,0 500,0 432,134 118,134" fill="var(--maroon)"/>
    </svg>
    <div class="logo-area">
      <div class="brand-name"><span class="brand-dot"></span>Harbel<br>Standwork</div>
    </div>
    <div class="copy">
      <div class="block">Client Follow-Up<br><span class="accent">Made Simple</span></div>
      <div class="divider"></div>
      <div class="block-2">Virtually No Cost To<br><span class="accent">Your Company!</span></div>
    </div>
    <a class="cta">
      <svg width="22" height="22" viewBox="0 0 24 24" aria-hidden="true"><path fill="#fff" d="M6.6 10.8a15 15 0 0 0 6.6 6.6l2.2-2.2c.3-.3.7-.4 1-.2 1.1.4 2.3.6 3.6.6.6 0 1 .4 1 1V20c0 .6-.4 1-1 1A17 17 0 0 1 3 4c0-.6.4-1 1-1h3.5c.6 0 1 .4 1 1 0 1.3.2 2.5.6 3.6.1.3 0 .7-.2 1z"/><path d="M14 3a7 7 0 0 1 7 7M14 6.5a3.5 3.5 0 0 1 3.5 3.5" stroke="#fff" stroke-width="1.6" fill="none"/></svg>
      <span class="cta-label">Call To Action</span>
      <svg width="26" height="26" viewBox="0 0 24 24" aria-hidden="true"><circle cx="12" cy="12" r="10.5" fill="#fff"/><path d="M7 10h5V6.5L17.5 12 12 17.5V14H7z" fill="var(--orange)"/></svg>
    </a>
  </section>

</body>
</html>
```